larkforge website

commerce website to sell cookeries, brackets, mailboxes and to show off homes built. Modern Steel in design see marlo cycles web page to be like: https://www.marlocycles-demo.com/en/ sorry its bright nest hosting word press divi

must be able to add products to page

Target Market(s)

mainly western states of U.S.

Industry/Entity Type

Building Product

Coding

Coded - Design and coding required

Number of Pages Required

3 page

Font styles to use
Sans Serif

Colors

Designer to choose colors to be used in the design.

Requirements
Must have
• customers to be able to order products from page
• bright nest hosting word press divi

```html
<!DOCTYPE html>
<html lang="en">
<head>
<meta charset="utf-8">
<title>Larkforge Steel</title>
<link href="https://fonts.googleapis.com/css2?family=Poppins:wght@400;500;600;700&family=Open+Sans:wght@400;600;700&display=swap" rel="stylesheet">
<style>
:root{
  --navy:#4a5a8c;
  --navy-dark:#3d4b78;
  --ink:#222428;
  --muted:#7a7d85;
  --line:#dcdde2;
  --star:#f2a51a;
  --red:#d8262c;
  --band:#eceef2;
  --white:#ffffff;
}
*{box-sizing:border-box;margin:0;padding:0}
html,body{width:1200px;height:3696px;overflow:hidden}
body{font-family:"Open Sans",sans-serif;color:var(--ink);background:var(--white);position:relative}
.abs{position:absolute}
h2.section-title{font-family:"Poppins",sans-serif;font-weight:500;font-size:38px;text-align:center;color:var(--ink)}

/* hero */
.hero{position:absolute;left:0;top:0;width:1200px;height:630px;
  background:linear-gradient(180deg,#3a3836 0%,#6b5443 40%,#8a4a26 60%,#2f2b29 100%)}
.hero-shade{position:absolute;inset:0;background:rgba(20,22,30,.35)}
.nav{position:absolute;left:0;top:0;width:1200px;height:80px;display:flex;align-items:center;padding:0 120px}
.brand{display:flex;align-items:center;gap:10px;color:var(--white);font-family:"Poppins",sans-serif;font-weight:600;font-size:22px;letter-spacing:2px}
.brand-mark{width:14px;height:14px;background:var(--white)}
.nav-links{margin-left:auto;display:flex;gap:34px;align-items:center;font-family:"Poppins",sans-serif;font-size:13px;font-weight:500;color:var(--white);letter-spacing:.5px}
.nav-links .active{border-bottom:2px solid var(--white);padding-bottom:4px}
.nav-search{width:38px;height:38px;border-radius:50%;background:var(--white);display:flex;align-items:center;justify-content:center}
.hero-title{position:absolute;top:222px;width:100%;text-align:center;font-family:"Poppins",sans-serif;font-weight:700;font-size:62px;letter-spacing:4px;color:var(--white)}
.hero-sub{position:absolute;top:316px;left:380px;width:440px;text-align:center;color:var(--white);font-size:14px;line-height:22px}
.btn-shop{position:absolute;top:424px;left:538px;width:124px;height:38px;background:var(--navy);color:var(--white);font-family:"Poppins",sans-serif;font-size:12px;font-weight:600;display:flex;align-items:center;justify-content:center;gap:8px}

/* products */
.product-row{position:absolute;left:112px;width:976px;display:flex;justify-content:space-between}
.product-card{width:236px;height:340px;border:1px solid var(--line);background:var(--white);position:relative;text-align:center}
.product-card.raised{box-shadow:0 8px 24px rgba(0,0,0,.18);border-color:transparent;top:-14px}
.product-photo{margin:28px auto 0;width:170px;height:150px;background:linear-gradient(180deg,#e9eaec,#9a9ca0 60%,#3a3b3e)}
.product-title{margin-top:30px;font-family:"Poppins",sans-serif;font-weight:600;font-size:14px}
.price-line{margin-top:12px;display:flex;justify-content:center;align-items:center;gap:18px}
.stars{color:var(--star);font-size:15px;letter-spacing:1px}
.price{font-family:"Poppins",sans-serif;font-size:22px}
.btn-cart{margin:18px auto 0;width:110px;height:30px;border:1px solid var(--navy);color:var(--navy);font-size:11px;font-weight:600;display:flex;align-items:center;justify-content:center;gap:6px}
.raised .btn-cart{background:var(--navy);color:var(--white)}
.badge-new{position:absolute;left:118px;top:10px;background:var(--red);color:var(--white);font-size:10px;font-weight:700;padding:5px 10px}
.quick-icons{position:absolute;right:12px;top:12px;display:flex;flex-direction:column;gap:6px}
.quick-icons span{width:24px;height:24px;border:1px solid var(--navy);display:block}

/* testimonials */
.testimonials{position:absolute;left:0;top:1320px;width:1200px;height:540px;background:linear-gradient(120deg,#f3f4f6,#dfe2e8 50%,#eef0f3)}
.quote-row{position:absolute;left:112px;top:192px;width:976px;display:flex;justify-content:space-between}
.quote-card{width:312px;height:266px;background:var(--white);box-shadow:0 2px 10px rgba(0,0,0,.08);padding:24px 26px}
.quote-mark{font-family:"Poppins",sans-serif;font-size:44px;line-height:30px;color:var(--navy);font-weight:700}
.quote-text{margin-top:18px;font-size:13px;line-height:21px;color:var(--muted)}
.quote-person{margin-top:24px;display:flex;align-items:center;gap:14px}
.avatar{width:44px;height:44px;border-radius:50%;background:#c9a58c}
.person-name{font-family:"Poppins",sans-serif;font-size:13px;font-weight:600}
.person-role{font-size:12px;color:var(--muted)}

/* news */
.news-feature{position:absolute;left:112px;top:2672px;width:488px;height:468px;border:1px solid var(--line)}
.news-feature-photo{height:240px;background:linear-gradient(180deg,#3b2a22,#b0603a 55%,#5a3326)}
.date-badge{position:absolute;right:22px;top:202px;width:56px;height:58px;background:var(--navy);color:var(--white);text-align:center;font-family:"Poppins",sans-serif;font-size:20px;font-weight:600;line-height:1.1;padding-top:8px}
.date-badge small{display:block;font-size:11px;font-weight:500}
.news-body{padding:42px 26px 0}
.news-heading{font-family:"Poppins",sans-serif;font-weight:600;font-size:14px}
.news-text{margin-top:14px;font-size:13px;line-height:21px;color:var(--muted)}
.read-more{margin-top:14px;font-size:13px;font-weight:600;color:var(--navy);border-bottom:1px solid var(--navy);display:inline-block}
.news-list{position:absolute;left:608px;top:2672px;width:480px}
.news-item{display:flex;height:148px;margin-bottom:12px}
.news-thumb{width:160px;height:148px;background:linear-gradient(180deg,#5e5a55,#a0683f 55%,#34302c)}
.news-item-body{flex:1;border:1px solid var(--line);border-left:none;padding:22px 22px}
.news-date{margin-top:6px;font-size:12px;color:var(--ink)}
.news-item-body .news-text{margin-top:8px;font-size:12px;line-height:19px}

/* footer */
.footer{position:absolute;left:0;top:3240px;width:1200px;height:456px;background:var(--navy);color:var(--white)}
.newsletter-title{position:absolute;left:176px;top:44px;font-family:"Poppins",sans-serif;font-size:19px;font-weight:500}
.newsletter-input{position:absolute;left:476px;top:34px;width:406px;height:48px;background:var(--white);color:var(--muted);font-size:13px;display:flex;align-items:center;padding-left:20px;gap:10px}
.newsletter-btn{position:absolute;left:882px;top:34px;width:142px;height:48px;background:var(--navy-dark);border:2px solid var(--white);font-family:"Poppins",sans-serif;font-size:13px;font-weight:600;display:flex;align-items:center;justify-content:center}
.footer-about{position:absolute;left:112px;top:140px;width:270px}
.footer-brand{display:flex;align-items:center;gap:10px;font-family:"Poppins",sans-serif;font-size:24px;font-weight:600;letter-spacing:2px}
.footer-about p{margin-top:16px;font-size:13px;line-height:21px;opacity:.9}
.social{margin-top:16px;display:flex;gap:10px}
.social span{width:30px;height:30px;border:1.5px solid var(--white);border-radius:50%}
.footer-col{position:absolute;top:140px;font-size:13px;line-height:20px}
.footer-col h4{font-family:"Poppins",sans-serif;font-size:13px;font-weight:600;border-bottom:1px solid rgba(255,255,255,.5);padding-bottom:6px;margin-bottom:14px}
.contact-line{display:flex;gap:10px;margin-bottom:16px;align-items:flex-start}
.contact-phone{font-family:"Poppins",sans-serif;font-size:18px;font-weight:600}
.link-list li{list-style:none;margin-bottom:10px}
.link-list li::before{content:"›";margin-right:8px}
.copyright{position:absolute;left:0;bottom:0;width:1200px;height:60px;background:var(--navy-dark);display:flex;align-items:center;justify-content:center;font-size:13px}
</style>
</head>
<body>

<header class="hero" role="img" aria-label="Photo of a steel fire pit with open flames and a mesh spark screen">
  <div class="hero-shade"></div>
  <nav class="nav">
    <div class="brand"><span class="brand-mark"></span>LARKFORGE</div>
    <div class="nav-links">
      <span class="active">HOME</span><span>ABOUT US</span><span>OUR PRODUCTS</span><span>LATEST BLOG</span><span>CONTACT US</span>
      <svg width="20" height="18" viewBox="0 0 20 18"><path d="M1 2h3l2.5 10h10L19 5H6" fill="none" stroke="#fff" stroke-width="1.8"/><circle cx="8" cy="15.5" r="1.5" fill="#fff"/><circle cx="15" cy="15.5" r="1.5" fill="#fff"/></svg>
      <span class="nav-search"><svg width="16" height="16" viewBox="0 0 16 16"><circle cx="7" cy="7" r="5" fill="none" stroke="#4a5a8c" stroke-width="2"/><path d="M11 11l4 4" stroke="#4a5a8c" stroke-width="2"/></svg></span>
    </div>
  </nav>
  <h1 class="hero-title">LARKFORGE STEEL</h1>
  <p class="hero-sub">Forged steel fire pits, grills and mailboxes built to last through every western season outdoors.</p>
  <div class="btn-shop">SHOP NOW <svg width="12" height="12" viewBox="0 0 12 12"><path d="M6 1l1.5 3.2 3.5.4-2.6 2.4.7 3.5L6 8.8 2.9 10.5l.7-3.5L1 4.6l3.5-.4z" fill="#fff"/></svg></div>
</header>

<h2 class="section-title abs" style="top:724px;left:0;width:1200px">Featured Products</h2>
<div class="product-row" style="top:860px">
  <div class="product-card"><div class="product-photo" role="img" aria-label="Square steel fire pit table"></div><div class="product-title">PRODUCT TITLE</div><div class="price-line"><span class="stars">★★★★★</span><span class="price">$ 46.00</span></div><div class="btn-cart">ADD TO CART</div></div>
  <div class="product-card"><div class="product-photo" role="img" aria-label="Black kettle charcoal grill"></div><div class="product-title">PRODUCT TITLE</div><div class="price-line"><span class="stars">★★★★★</span><span class="price">$ 46.00</span></div><div class="btn-cart">ADD TO CART</div></div>
  <div class="product-card"><div class="product-photo" role="img" aria-label="Round fire bowl on steel legs"></div><div class="product-title">PRODUCT TITLE</div><div class="price-line"><span class="stars">★★★★★</span><span class="price">$ 46.00</span></div><div class="btn-cart">ADD TO CART</div></div>
  <div class="product-card"><div class="product-photo" role="img" aria-label="Round steel grill with cooking grate"></div><div class="product-title">PRODUCT TITLE</div><div class="price-line"><span class="stars">★★★★★</span><span class="price">$ 46.00</span></div><div class="btn-cart">ADD TO CART</div></div>
</div>

<section class="testimonials" role="img" aria-label="Faint background photo of outdoor steel grills">
  <h2 class="section-title abs" style="top:104px;left:0;width:1200px">Our Testimonials</h2>
  <div class="quote-row">
    <div class="quote-card"><div class="quote-mark">“</div><p class="quote-text">Sed ut perspiciatis unde omnis iste natus error sit voluptatem accusantium doloremque laudantium, totam rem aperiam, eaque ipsa quae.</p><div class="quote-person"><span class="avatar" role="img" aria-label="Customer portrait"></span><div><div class="person-name">RENWICK</div><div class="person-role">Businessman</div></div></div></div>
    <div class="quote-card"><div class="quote-mark">“</div><p class="quote-text">Sed ut perspiciatis unde omnis iste natus error sit voluptatem accusantium doloremque laudantium, totam rem aperiam, eaque ipsa quae.</p><div class="quote-person"><span class="avatar" role="img" aria-label="Customer portrait"></span><div><div class="person-name">RENWICK</div><div class="person-role">Businessman</div></div></div></div>
    <div class="quote-card"><div class="quote-mark">“</div><p class="quote-text">Sed ut perspiciatis unde omnis iste natus error sit voluptatem accusantium doloremque laudantium, totam rem aperiam, eaque ipsa quae.</p><div class="quote-person"><span class="avatar" role="img" aria-label="Customer portrait"></span><div><div class="person-name">RENWICK</div><div class="person-role">Businessman</div></div></div></div>
  </div>
</section>

<h2 class="section-title abs" style="top:1956px;left:0;width:1200px">Popular Products</h2>
<div class="product-row" style="top:2084px">
  <div class="product-card"><span class="badge-new">NEW ITEM</span><div class="product-photo" role="img" aria-label="Square steel fire pit table"></div><div class="product-title">PRODUCT TITLE</div><div class="price-line"><span class="stars">★★★★★</span><span class="price">$ 46.00</span></div><div class="btn-cart">ADD TO CART</div></div>
  <div class="product-card"><div class="product-photo" role="img" aria-label="Black kettle charcoal grill"></div><div class="product-title">PRODUCT TITLE</div><div class="price-line"><span class="stars">★★★★★</span><span class="price">$ 46.00</span></div><div class="btn-cart">ADD TO CART</div></div>
  <div class="product-card raised"><div class="quick-icons"><span></span><span></span><span></span></div><div class="product-photo" role="img" aria-label="Round fire bowl on steel legs"></div><div class="product-title">PRODUCT TITLE</div><div class="price-line"><span class="stars">★★★★★</span><span class="price">$ 46.00</span></div><div class="btn-cart">ADD TO CART</div></div>
  <div class="product-card"><div class="product-photo" role="img" aria-label="Round steel grill with cooking grate"></div><div class="product-title">PRODUCT TITLE</div><div class="price-line"><span class="stars">★★★★★</span><span class="price">$ 46.00</span></div><div class="btn-cart">ADD TO CART</div></div>
</div>

<h2 class="section-title abs" style="top:2544px;left:0;width:1200px">Latest News</h2>
<article class="news-feature">
  <div class="news-feature-photo" role="img" aria-label="Meat cooking over a flaming grill"></div>
  <div class="date-badge">29<small>JAN</small></div>
  <div class="news-body">
    <div class="news-heading">LOREM IPSUM DOLOR SIT AMET</div>
    <p class="news-text">Sed ut perspiciatis unde omnis iste natus error sit voluptatem accusantium doloremque laudantium, totam rem aperiam eaque ipsa.</p>
    <span class="read-more">READ MORE »</span>
  </div>
</article>
<div class="news-list">
  <div class="news-item"><div class="news-thumb" role="img" aria-label="Steaks searing on a grill"></div><div class="news-item-body"><div class="news-heading">LOREM IPSUM DOLOR SIT AMET</div><div class="news-date">27 JAN 2020</div><p class="news-text">Sed ut perspiciatis unde omnis iste natus error sit voluptatem.</p></div></div>
  <div class="news-item"><div class="news-thumb" role="img" aria-label="Row of grills outdoors"></div><div class="news-item-body"><div class="news-heading">LOREM IPSUM DOLOR SIT AMET</div><div class="news-date">27 JAN 2020</div><p class="news-text">Sed ut perspiciatis unde omnis iste natus error sit voluptatem.</p></div></div>
  <div class="news-item"><div class="news-thumb" role="img" aria-label="Vegetables roasting in a pan over fire"></div><div class="news-item-body"><div class="news-heading">LOREM IPSUM DOLOR SIT AMET</div><div class="news-date">27 JAN 2020</div><p class="news-text">Sed ut perspiciatis unde omnis iste natus error sit voluptatem.</p></div></div>
</div>

<footer class="footer">
  <div class="newsletter-title">SIGN UP FOR NEWSLETTER</div>
  <div class="newsletter-input"><svg width="16" height="12" viewBox="0 0 16 12"><rect x="1" y="1" width="14" height="10" fill="none" stroke="#7a7d85" stroke-width="1.4"/><path d="M1 1l7 6 7-6" fill="none" stroke="#7a7d85" stroke-width="1.4"/></svg>Enter Your Email</div>
  <div class="newsletter-btn">SUBSCRIBE</div>

  <div class="footer-about">
    <div class="footer-brand"><span class="brand-mark"></span>LARKFORGE</div>
    <p>Steel cookware, brackets and mailboxes forged for western homes, made to order and shipped with care.</p>
    <div class="social"><span></span><span></span><span></span><span></span></div>
  </div>

  <div class="footer-col" style="left:468px;width:240px">
    <h4>CONTACT US</h4>
    <div class="contact-line"><svg width="14" height="18" viewBox="0 0 14 18"><path d="M7 1a5.5 5.5 0 0 0-5.5 5.5C1.5 11 7 17 7 17s5.5-6 5.5-10.5A5.5 5.5 0 0 0 7 1z" fill="none" stroke="#fff" stroke-width="1.5"/><circle cx="7" cy="6.5" r="2" fill="#fff"/></svg><span>555 Lorem Ipsum Avenue<br>United States</span></div>
    <div class="contact-line"><svg width="16" height="12" viewBox="0 0 16 12"><rect x="1" y="1" width="14" height="10" fill="none" stroke="#fff" stroke-width="1.4"/><path d="M1 1l7 6 7-6" fill="none" stroke="#fff" stroke-width="1.4"/></svg><span>hello@larkforge.com</span></div>
    <div class="contact-line"><svg width="16" height="16" viewBox="0 0 16 16"><path d="M3 1h3l1.5 4-2 1.2a9 9 0 0 0 4.3 4.3L11 8.5l4 1.5v3a2 2 0 0 1-2 2A12 12 0 0 1 1 3a2 2 0 0 1 2-2z" fill="#fff"/></svg><span class="contact-phone">555 010 4477</span></div>
  </div>

  <div class="footer-col" style="left:780px;width:130px">
    <h4>QUICK LINKS</h4>
    <ul class="link-list"><li>Home</li><li>About Us</li><li>Our Products</li><li>Latest News</li><li>Reviews</li></ul>
  </div>

  <div class="footer-col" style="left:956px;width:132px">
    <h4>OTHER LINKS</h4>
    <ul class="link-list"><li>Contact Us</li><li>FAQ</li><li>Help Section</li><li>Terms Of Use</li><li>Privacy Policy</li></ul>
  </div>

  <div class="copyright">© 2020 Larkforge Steel. All Rights Reserved.</div>
</footer>

</body>
</html>
```